Web Design Project

We are an online tax Continuing education provider. We provide online courses for tax preparers. We want the front end page to be user friendly and for the buyer to know exactly what they are looking at. We want a front end page to look smiliar www.larkvalefiling.com. It should have a similar feel to this one.
Our website address will be www.7782QX.com
We currently have another website that is www.LedgrUMs.com but we do not want it to look like this. We want a different look but same information.
We have a logo already which is attached. We don't have specific colors in mind for the front page but don't want it to be too busy looking. It should stand out but not too simple either.
Target Market(s)
Tax Preparers. More serious and professional but these folks are usually not tech savy. Simple, easy to use, and functional is key.
Industry/Entity Type
Education
Requirements
Must have
- Use standard HTML & CSS. NO other coding is needed.
We are looking for 5-7 pages including Home page, log in, FAQ.
Please look at our current website www.LedgrUMs.com and also www.larkvalefiling.com

```html
<!DOCTYPE html>
<html lang="en">
<head>
<meta charset="utf-8">
<title>7782QX – Continuing Education for Tax Preparers</title>
<link href="https://fonts.googleapis.com/css2?family=Ubuntu:wght@300;400;500&family=PT+Sans:wght@400;700&family=Lora&display=swap" rel="stylesheet">
<style>
:root{
  --green:#a8c31d;
  --navy:#0e2b4d;
  --blue:#1a8fcf;
  --blue-light:#43b2e6;
  --orange:#f27512;
  --accent:#e0641a;
  --text:#444;
  --muted:#666;
  --card:#f4f4f4;
  --footer:#ececec;
  --bar:#d8d8d8;
  --dark:#2b2b2b;
}
*{margin:0;padding:0;box-sizing:border-box}
html,body{width:832px;height:1200px;overflow:hidden}
body{position:relative;background:#fff;font-family:"PT Sans",sans-serif;color:var(--text)}
.abs{position:absolute}

.brand{left:34px;top:30px;font:500 28px/1 "Ubuntu",sans-serif;color:var(--navy)}
.phone{left:678px;top:16px;display:flex;align-items:center;gap:6px;font:400 16px "Ubuntu",sans-serif;color:#555}
.nav{left:475px;top:66px;width:332px;height:32px;display:flex;background:var(--dark);box-shadow:0 2px 3px rgba(0,0,0,.3)}
.nav a{color:#fff;text-decoration:none;font:400 11px/32px "Ubuntu",sans-serif;text-align:center;border-right:1px solid #444}
.nav a.active{background:var(--green)}

.hero{left:0;top:104px;width:832px;height:288px;background:linear-gradient(180deg,var(--blue) 0%,var(--blue-light) 60%,#7fcff0 100%)}
.hero-frame{left:34px;top:24px;width:420px;height:238px;background:var(--green);padding:5px;box-shadow:0 4px 6px rgba(0,0,0,.3)}
.hero-art{width:100%;height:100%;background:linear-gradient(135deg,#ffffff,#e6eef3)}
.hero-title{left:488px;top:54px;font:400 16px "Ubuntu",sans-serif;color:#fff}
.hero-list{left:518px;top:94px;list-style:none;font:300 18px/29px "Ubuntu",sans-serif;color:#fff}
.hero-list li::before{content:"› ";font-weight:500}
.hero-tag{left:528px;top:198px;font:400 16px "Ubuntu",sans-serif;color:#fff}
.dots{left:716px;top:252px;display:flex;gap:3px}
.dots span{width:8px;height:8px;border-radius:50%;background:var(--navy)}
.dots span.on{background:var(--green);border:2px solid var(--navy)}

.plan{top:416px;width:230px;height:282px;background:var(--card);box-shadow:0 1px 3px rgba(0,0,0,.25)}
.price{position:absolute;left:62px;top:2px;width:94px;height:56px;background:var(--green);color:#fff;font:400 24px/52px "Lora",serif;text-align:center}
.price small{font-size:13px}
.plan-title{position:absolute;left:12px;top:62px;width:206px;font-size:10.5px;line-height:21px;color:#444;border-bottom:1px dashed #bbb;padding-bottom:4px}
.plan-items{position:absolute;left:7px;top:114px;list-style:none;font-size:8.5px;line-height:25px;color:#444}
.plan-items li::before{content:"› ";font-weight:700}
.plan-more{position:absolute;left:7px;top:218px;width:216px;border-top:1px dashed #bbb;text-align:right;font-size:8.5px;color:#c43c12;padding:6px 6px 0}
.register{position:absolute;left:0;bottom:0;width:230px;height:38px;background:var(--navy);color:#fff;font:400 14px/38px "Ubuntu",sans-serif;text-align:center}

.about{left:35px;top:718px;width:496px;height:312px;border:1px solid #ccc;border-radius:4px;background:linear-gradient(#fff,#f7f7f7)}
.about ul{position:absolute;left:32px;top:24px;list-style:none;font-size:10.5px;line-height:28.8px;color:#444}
.about li::before{content:"›";display:inline-block;width:10px;height:10px;margin-right:8px;border:1px solid var(--orange);color:var(--orange);font-size:8px;line-height:8px;text-align:center}
.about-note{position:absolute;left:33px;top:210px;font-size:10px;color:#444}
.bulletin{position:absolute;left:64px;top:240px;width:311px;height:42px;background:linear-gradient(var(--orange),#e25e06);border-radius:3px;box-shadow:2px 3px 4px rgba(0,0,0,.35);color:#fff;font:400 13px/38px "Ubuntu",sans-serif;padding-left:29px}

.testimonials{left:568px;top:722px;width:220px}
.testimonials h2{font:400 16px "Ubuntu",sans-serif;color:var(--accent);border-bottom:1px solid #ddd;padding-bottom:4px}
.quote{position:relative;height:96px;margin-top:10px}
.quote .photo{position:absolute;left:8px;top:0;width:48px;height:44px;background:linear-gradient(#8c9a7a,#4f5a48);border:1px solid #ccc}
.quote p{position:absolute;left:68px;top:0;width:152px;font-size:8.5px;line-height:14.4px;color:#555;text-align:justify}
.quote cite{position:absolute;right:0;font-style:normal;font-size:8.5px;color:var(--accent)}
.view-more{position:absolute;right:0;top:290px;font-size:8.5px;color:var(--accent)}

.footer{left:0;top:1050px;width:832px;height:108px;background:var(--footer)}
.badge{position:absolute}
.divider{position:absolute;left:302px;top:12px;width:1px;height:90px;background:#bbb}
.footer-brand{position:absolute;left:720px;top:38px;font:500 22px "Ubuntu",sans-serif;color:var(--navy)}
.bottom{left:0;top:1158px;width:832px;height:42px;background:var(--bar)}
.social{position:absolute;left:50px;top:14px;display:flex;gap:6px}
.social span{width:22px;height:22px;border-radius:50%;background:#3b6fb6}
.social span:last-child{background:#e8601c}
.footer-links{position:absolute;right:22px;top:9px;font-size:9px;color:#333}
.copyright{position:absolute;right:22px;top:28px;font-size:8.5px;color:#444}
</style>
</head>
<body>

<header>
  <div class="abs brand">7782QX</div>
  <div class="abs phone">
    <svg width="20" height="22" viewBox="0 0 20 22"><path d="M4 1 L8 6 L6 9 Q8 14 12 16 L15 14 L19 18 L16 21 Q8 21 3 13 Q0 7 1 3 Z" fill="#444"/></svg>
    800-555-0142
  </div>
  <nav class="abs nav">
    <a class="active" style="width:56px" href="#">Home</a>
    <a style="width:78px" href="#">Courses</a>
    <a style="width:55px" href="#">FAQ</a>
    <a style="width:72px" href="#">Contact</a>
    <a style="width:71px;border:0" href="#">Sign In</a>
  </nav>
</header>

<section class="abs hero">
  <div class="abs hero-frame"><div class="hero-art" role="img" aria-label="Stack of books with graduation cap, diploma and computer mouse"></div></div>
  <h1 class="abs hero-title" style="font-weight:400">Continuing Education made simple!</h1>
  <ul class="abs hero-list"><li>Fast</li><li>Easy</li><li>Low Cost</li></ul>
  <p class="abs hero-tag">Completely Online! “Self-paced”</p>
  <div class="abs dots"><span></span><span></span><span class="on"></span></div>
</section>

<section class="abs plan" style="left:37px">
  <div class="price">$42</div>
  <p class="plan-title">15-Hour package for IRS Registered Tax-Preparer Continuing Education:</p>
  <ul class="plan-items"><li>Ethics (2 hrs CE Credit)</li><li>Charitable Contributions 101 (3 hrs CE Credit)</li><li>Earned Income Credit (2 hrs CE Credit)</li><li>Deducting Transportation Expenses (2 hrs CE Credit)</li></ul>
  <div class="plan-more">More Information</div>
  <div class="register">CLICK HERE TO REGISTER</div>
</section>
<section class="abs plan" style="left:302px">
  <div class="price">$79<small>.90</small></div>
  <p class="plan-title">RTRP Exam Preparation Course 10CE Credit</p>
  <ul class="plan-items"><li>Ethics (2 hrs CE Credit)</li><li>Charitable Contributions 101 (3 hrs CE Credit)</li><li>Earned Income Credit (2 hrs CE Credit)</li><li>Deducting Transportation Expenses (2 hrs CE Credit)</li></ul>
  <div class="plan-more">More Information</div>
  <div class="register">CLICK HERE TO REGISTER</div>
</section>
<section class="abs plan" style="left:567px">
  <div class="price">$99<small>.90</small></div>
  <p class="plan-title">Combo Package RTRP Exam Preparation Course 15 hours CE Credit</p>
  <ul class="plan-items"><li>Ethics (2 hrs CE Credit)</li><li>Charitable Contributions 101 (3 hrs CE Credit)</li><li>Earned Income Credit (2 hrs CE Credit)</li><li>Deducting Transportation Expenses (2 hrs CE Credit)</li></ul>
  <div class="plan-more">More Information</div>
  <div class="register">CLICK HERE TO REGISTER</div>
</section>

<section class="abs about">
  <ul>
    <li>We are your official source for registered tax-preparer continuing education.</li>
    <li>IRS-approved provider ( Provider Id 7QXLE).</li>
    <li>Easy to understand</li>
    <li>Relevant, up-to-date materials</li>
    <li>Printable Certificate of Completion</li>
    <li>We report CE hours directly to IRS after completion</li>
  </ul>
  <p class="about-note">IRS Latest Information Link ( Click button to open IRS document or link)</p>
  <div class="bulletin">RTRP Test Candidate Information Bulletin</div>
</section>

<aside class="abs testimonials">
  <h2>Testimonials</h2>
  <div class="quote" style="height:74px">
    <div class="photo" role="img" aria-label="Customer portrait"></div>
    <p>Great reading materials! I learned a lot that I did not know previously. I'm so glad I chose your program!!!!</p>
    <cite style="top:50px">Rowan.AK</cite>
  </div>
  <div class="quote" style="height:86px">
    <div class="photo" role="img" aria-label="Customer portrait"></div>
    <p>The class was very convenient because I work crazy hours ... the pace was great. I learned some laws that I wasn't aware of to help my clients. I</p>
    <cite style="top:64px">-Delia.Tx</cite>
  </div>
  <div class="quote">
    <div class="photo" role="img" aria-label="Customer portrait"></div>
    <p>Great reading materials! I learned a lot that I did not know previously. I'm so glad I chose your program!!!!</p>
    <cite style="top:42px">Maren.Tx</cite>
  </div>
  <span class="view-more">View More &gt;&gt;</span>
</aside>

<footer class="abs footer">
  <div class="badge" style="left:46px;top:18px;width:75px;height:82px;background:linear-gradient(#3c8fd8,#1f62b0)" aria-label="Approved provider badge" role="img"></div>
  <div class="badge" style="left:158px;top:18px;width:73px;height:82px;background:linear-gradient(#e8e2c4,#2a7fcf)" aria-label="Certificate of completion badge" role="img"></div>
  <div class="divider"></div>
  <div class="badge" style="left:356px;top:36px;width:214px;height:50px;background:#dcdcdc;border:1px solid #c4c4c4" aria-label="Continuing education accreditor badge" role="img"></div>
  <div class="badge" style="left:609px;top:42px;width:71px;height:38px;background:#f3b233;border:2px solid #7a1c10" aria-label="Security certificate badge" role="img"></div>
  <div class="footer-brand">7782QX</div>
</footer>

<div class="abs bottom">
  <div class="social"><span></span><span></span><span></span><span></span></div>
  <div class="footer-links">Home &nbsp;| &nbsp;Policy &nbsp;| &nbsp;Contact Us &nbsp;| &nbsp;FAQ &nbsp;| &nbsp;Admin</div>
  <div class="copyright">© 2013 LedgrUMs, All Rights Reserved</div>
</div>

</body>
</html>
```